Cedarvale Ridge College

We are looking to update our current webpage at www.cedarvaleridge.ca. We would like to make it modern, fresh and appealing to students. We want to keep our logo the same with the logo colours blended in as the primary colours and focus. We are open to reconfiguring content as well.
Reason: Hi, In the next 3 days we will have narrowed our search to 3 designs and will make a choice before the final deadline...
College

```html
<!DOCTYPE html>
<html lang="en">
<head>
<meta charset="utf-8">
<title>Cedarvale Ridge College</title>
<link rel="stylesheet" href="https://fonts.googleapis.com/css2?family=Arvo:wght@400;700&family=Lato:wght@400;700;900&display=swap">
<style>
:root{
  --navy:#0f1f52;
  --navy-deep:#0b1740;
  --navy-bar:#142658;
  --ink:#222;
  --muted:#555;
  --light:#ededed;
  --white:#fff;
  --footer:#0a0f22;
  --rule:#c9c9c9;
}
*{box-sizing:border-box;margin:0;padding:0}
html,body{width:1200px;height:2824px;overflow:hidden}
body{font-family:"Lato",Arial,sans-serif;color:var(--ink);background:var(--white);position:relative}
.serif{font-family:"Arvo",Georgia,serif}
.abs{position:absolute}
.btn{display:inline-block;background:var(--navy);color:#fff;font-weight:700;font-size:17px;border-radius:8px;padding:0 28px;height:36px;line-height:36px;text-align:center}

/* header */
.site-header{position:absolute;left:0;top:0;width:1200px;height:122px;background:#fff}
.util-tabs{position:absolute;left:616px;top:0;width:448px;height:24px;background:var(--navy);border-radius:0 0 10px 10px;display:flex;justify-content:space-around;align-items:center;color:#fff;font-size:13px;font-weight:700}
.util-tabs::after{content:"";position:absolute;right:-26px;top:0;width:26px;height:26px;border-radius:50%;border:2px solid var(--navy);background:#fff}
.brand{position:absolute;left:134px;top:30px;display:flex;align-items:center;gap:12px}
.brand-mark{width:40px;height:40px;background:var(--navy)}
.brand-name{font-family:"Arvo",Georgia,serif;font-weight:700;font-size:25px;color:var(--navy);line-height:1.05;width:200px}
.search{position:absolute;left:725px;top:56px;width:176px;height:31px;border:1px solid #bbb;display:flex}
.search span{flex:1;font-size:11px;color:#999;padding:9px 8px}
.search i{width:30px;background:#8a8a8a}
.social{position:absolute;left:918px;top:55px;display:flex;gap:8px}
.social b{width:32px;height:32px;border-radius:50%;border:2px solid var(--navy)}
.social b:last-child{border-color:#c0392b;background:#c0392b}

.main-nav{position:absolute;left:0;top:122px;width:1200px;height:43px;background:#0d1533}
.main-nav ul{list-style:none;display:flex;position:absolute;left:134px;top:0;height:43px;align-items:center;gap:0}
.main-nav li{color:#fff;font-size:15px;padding:0 18px;height:43px;line-height:43px}
.main-nav li.active{background:#2a2f3e;font-weight:700}

/* hero */
.hero{position:absolute;left:0;top:165px;width:1200px;height:520px;overflow:hidden}
.hero-photo{position:absolute;inset:0;background:linear-gradient(180deg,#0d1a3d 0%,#1f3357 35%,#3b3a35 55%,#8a5a2a 78%,#b57535 100%)}
.hero h1{position:absolute;top:293px;width:100%;text-align:center;color:#fff;font-size:33px;font-weight:900;letter-spacing:.5px}
.hero p{position:absolute;top:343px;width:100%;text-align:center;color:#fff;font-size:14px}
.hero-form{position:absolute;top:383px;left:275px;display:flex;gap:36px}
.hero-form span{width:221px;height:36px;background:#fff;border-radius:6px;font-size:12px;color:#999;padding:11px 12px}
.hero-form .join{width:134px;background:var(--navy);color:#fff;font-weight:700;font-size:15px;text-align:center;padding:9px 0;border-radius:6px}
.hero-down{position:absolute;left:577px;top:447px}

/* welcome */
.welcome{position:absolute;top:685px;left:0;width:1200px;height:310px;text-align:center}
.section-title{font-family:"Arvo",Georgia,serif;font-weight:700;color:var(--navy);font-size:31px}
.welcome .section-title{margin-top:50px}
.title-rule{width:80px;height:2px;background:var(--navy);margin:10px auto 0}
.welcome p{width:1000px;margin:18px auto 0;font-size:14px;line-height:23px;color:#333}
.welcome .btn{margin-top:18px}

/* videos */
.videos{position:absolute;top:995px;left:0;width:1200px;height:285px;text-align:center;color:#fff}
.videos-photo{position:absolute;inset:0;background:linear-gradient(90deg,#2a2620,#3d3a33 30%,#2f4a3e 55%,#2b2a25)}
.videos-photo::after{content:"";position:absolute;inset:0;background:rgba(5,10,25,.55)}
.videos .in{position:relative}
.videos h2{font-family:"Arvo",Georgia,serif;font-size:31px;padding-top:38px}
.videos p{width:1000px;margin:14px auto 0;font-size:14px;line-height:23px}
.videos svg{margin-top:22px}

/* campus */
.campus{position:absolute;top:1280px;left:0;width:1200px;height:525px}
.campus .section-title{text-align:center;margin-top:47px}
.campus .wide-rule{width:330px;height:1px;background:var(--rule);margin:12px auto 0}
.card{position:absolute;top:115px;width:282px;text-align:center}
.card .frame{height:184px;border:1px solid #ddd;padding:7px;background:#fff}
.card .frame div{width:100%;height:100%}
.card h3{font-size:19px;color:var(--navy);font-weight:700;margin-top:20px}
.card p{font-size:15px;line-height:25px;color:#333;margin-top:8px;padding:0 6px}
.card .btn{margin-top:10px;padding:0 32px}

/* admissions & news */
.admissions{position:absolute;top:1805px;left:0;width:1200px;height:402px;background:var(--light)}
.admissions h2{position:absolute;top:57px;font-family:"Arvo",Georgia,serif;font-weight:700;color:var(--navy);font-size:29px}
.adm-list{position:absolute;left:134px;top:111px;list-style:none}
.adm-list li{height:35.5px;font-size:15px;color:#333;display:flex;align-items:center;gap:12px}
.news{position:absolute;top:117px;width:200px}
.news .frame{height:102px;background:#fff;padding:6px;border:1px solid #ddd}
.news .frame div{width:100%;height:100%}
.news .date{font-size:14px;font-weight:700;color:var(--navy);margin-top:22px}
.news p{font-size:15px;line-height:25px;color:#333;letter-spacing:.3px}
.news a{font-size:14px;color:var(--navy);text-decoration:none}

/* contact */
.contact{position:absolute;top:2207px;left:0;width:1200px;height:581px;background:var(--navy);color:#fff}
.contact .env{position:absolute;left:567px;top:54px}
.contact h2{position:absolute;top:129px;width:100%;text-align:center;font-size:27px;font-weight:400}
.contact .lead{position:absolute;top:172px;width:100%;text-align:center;font-size:14px;line-height:18px}
.contact .rule{position:absolute;top:223px;left:134px;width:932px;height:1px;background:rgba(255,255,255,.35)}
.contact h3{position:absolute;top:241px;font-family:"Arvo",Georgia,serif;font-weight:400;font-size:21px}
.field{position:absolute;left:141px;width:299px;background:#fff;border-radius:8px;color:#aaa;font-size:11px;padding:10px 12px}
.send{position:absolute;left:141px;top:487px;width:134px;height:36px;background:#000;border-radius:8px;text-align:center;line-height:36px;font-weight:700;font-size:15px}
.map{position:absolute;left:496px;top:283px;width:318px;height:195px;background:#fff;padding:6px}
.map div{width:100%;height:100%;background:linear-gradient(135deg,#e4e6df,#cfd9c6 60%,#e8e5da)}
.find{position:absolute;left:871px;top:283px;list-style:none;font-size:14px}
.find li{display:flex;gap:14px;margin-bottom:13px;line-height:19px}
.find li svg{flex:none;margin-top:2px}
.find .socials{display:flex;gap:18px;margin-top:4px}
.find .socials b{width:22px;height:22px;background:#fff}

.site-footer{position:absolute;top:2788px;left:0;width:1200px;height:36px;background:var(--footer);color:#ccc;font-size:12px;text-align:center;line-height:36px}
</style>
</head>
<body>

<header class="site-header">
  <nav class="util-tabs"><span>Apply Today</span><span>Donate</span><span>Library</span><span>Text For Info</span></nav>
  <div class="brand"><span class="brand-mark"></span><span class="brand-name">Cedarvale Ridge College</span></div>
  <div class="search"><span>Search your Subject</span><i></i></div>
  <div class="social"><b></b><b></b><b></b><b></b></div>
</header>

<nav class="main-nav">
  <ul>
    <li class="active">Home</li><li>About Us</li><li>Consider Cedarvale</li><li>Current students</li><li>Alumni</li><li>Supporters</li><li>News &amp; Event</li><li>Cedarvale Park</li>
  </ul>
</nav>

<section class="hero">
  <div class="hero-photo" role="img" aria-label="Campus buildings and parking lot at dusk with lit lamps"></div>
  <h1>WE WILL HELP YOU TO UNDERSTAND FRIENDLY COMPASS</h1>
  <p>Lorem ipsum dolor sit amet, consectetuer adipiscing elit, sed diam nonummy nibh euismod tincidunt ut laoreet dolore.</p>
  <div class="hero-form"><span>Name</span><span>Email Address</span><span class="join">JOIN NOW !</span></div>
  <svg class="hero-down" width="46" height="46" viewBox="0 0 46 46"><circle cx="23" cy="23" r="21" fill="none" stroke="#fff" stroke-width="2"/><path d="M14 19l9 9 9-9" fill="none" stroke="#fff" stroke-width="2.5"/></svg>
</section>

<section class="welcome">
  <h2 class="section-title">Welcome Cedarvale Ridge College</h2>
  <div class="title-rule"></div>
  <p>Lorem ipsum dolor sit amet, consectetur adipiscing elit. Aenean et dignissim sem, interdum risus. Vestibulum consectetur nisi mollis diam pulvinar adipiscing. Vestibulum ut urna nec nibh adipiscing facilisis. Etiam auctor porta lacus ac luctus. Praesent ac libero fermentum, rhoncus magna a, dapibus mauris. Nam ut auctor justo. Sed ante odio, luctus quis nequ nec, adipiscing eleifend arcu. Integer nunc turpis, porttitor at lorem ut. Etiam auctor porta lacus ac luctus. Praesent ac libero fermentum, rhoncus magna.</p>
  <span class="btn">Read More</span>
</section>

<section class="videos">
  <div class="videos-photo" role="img" aria-label="College entrance sign against a brick wall"></div>
  <div class="in">
    <h2>Cedarvale Videos</h2>
    <p>Lorem ipsum dolor sit amet, consectetur adipiscing elit. Aenean et dignissim sem, interdum risus. Vestibulum consectetur nisi mollis diam pulvinar adipiscing. Vestibulum ut urna nec nibh adipiscing facilisis. Etiam auctor porta lacus ac luctus. Praesent ac libero fermentum, rhoncus. consectetur adipiscing elit. Aenean et dignissim sem, interdum risus. Vestibulum consectetur nisi mollis diam pulvinar adipiscing.</p>
    <svg width="58" height="58" viewBox="0 0 58 58"><circle cx="29" cy="29" r="26" fill="none" stroke="#fff" stroke-width="3"/><path d="M23 18l17 11-17 11z" fill="#fff"/></svg>
  </div>
</section>

<section class="campus">
  <h2 class="section-title">Our Campus</h2>
  <div class="wide-rule"></div>
  <article class="card" style="left:134px">
    <div class="frame"><div role="img" aria-label="Aerial campus map with location markers" style="background:linear-gradient(135deg,#3b4a7a,#5a6a9a 50%,#2d3a5e)"></div></div>
    <h3>Campur Map</h3>
    <p>Lorem ipsum dolor sit amet, consectetur adipiscing elit. Aenean et dignissim sem, interdum risus. Vestibulum consectetu</p>
    <span class="btn">Read More</span>
  </article>
  <article class="card" style="left:461px">
    <div class="frame"><div role="img" aria-label="Street map showing the college location" style="background:linear-gradient(135deg,#e3e6dc,#cdd8c2 60%,#e6e2d4)"></div></div>
    <h3>Map &amp; Directions</h3>
    <p>Lorem ipsum dolor sit amet, consectetur adipiscing elit. Aenean et dignissim sem, interdum risus. Vestibulum consectetu</p>
    <span class="btn">Read More</span>
  </article>
  <article class="card" style="left:786px">
    <div class="frame"><div role="img" aria-label="Chapel interior with rows of chairs" style="background:linear-gradient(180deg,#c9a98a,#9a7a60 55%,#6b4a3a)"></div></div>
    <h3>Photo Tour</h3>
    <p>Lorem ipsum dolor sit amet, consectetur adipiscing elit. Aenean et dignissim sem, interdum risus. Vestibulum consectetu</p>
    <span class="btn">Read More</span>
  </article>
</section>

<section class="admissions">
  <h2 style="left:134px">Our Admissions</h2>
  <ul class="adm-list">
    <li><svg width="16" height="16" viewBox="0 0 16 16"><circle cx="8" cy="8" r="8" fill="#0f1f52"/><path d="M4 8l3 3 5-6" fill="none" stroke="#fff" stroke-width="2"/></svg>Download The Full Catalogue</li>
    <li><svg width="16" height="16" viewBox="0 0 16 16"><circle cx="8" cy="8" r="8" fill="#0f1f52"/><path d="M4 8l3 3 5-6" fill="none" stroke="#fff" stroke-width="2"/></svg>Apply Today (Application Package)</li>
    <li><svg width="16" height="16" viewBox="0 0 16 16"><circle cx="8" cy="8" r="8" fill="#0f1f52"/><path d="M4 8l3 3 5-6" fill="none" stroke="#fff" stroke-width="2"/></svg>Information Request</li>
    <li><svg width="16" height="16" viewBox="0 0 16 16"><circle cx="8" cy="8" r="8" fill="#0f1f52"/><path d="M4 8l3 3 5-6" fill="none" stroke="#fff" stroke-width="2"/></svg>Browse our Programs</li>
    <li><svg width="16" height="16" viewBox="0 0 16 16"><circle cx="8" cy="8" r="8" fill="#0f1f52"/><path d="M4 8l3 3 5-6" fill="none" stroke="#fff" stroke-width="2"/></svg>Download Forms</li>
    <li><svg width="16" height="16" viewBox="0 0 16 16"><circle cx="8" cy="8" r="8" fill="#0f1f52"/><path d="M4 8l3 3 5-6" fill="none" stroke="#fff" stroke-width="2"/></svg>Admissions Information</li>
    <li><svg width="16" height="16" viewBox="0 0 16 16"><circle cx="8" cy="8" r="8" fill="#0f1f52"/><path d="M4 8l3 3 5-6" fill="none" stroke="#fff" stroke-width="2"/></svg>Campus Directory</li>
  </ul>
  <h2 style="left:605px">News &amp; Event</h2>
  <article class="news" style="left:607px">
    <div class="frame"><div role="img" aria-label="Staff members at a campus event" style="background:linear-gradient(135deg,#dfe4ea,#a9b6c4)"></div></div>
    <div class="date">November 22, 2014</div>
    <p>Lorem ipsum dolor sit amet consectetur adipiscing elit.</p>
    <a>Read More »</a>
  </article>
  <article class="news" style="left:866px">
    <div class="frame"><div role="img" aria-label="Students talking in a bright room" style="background:linear-gradient(135deg,#e6e3df,#b9a89a)"></div></div>
    <div class="date">November 22, 2014</div>
    <p>Lorem ipsum dolor sit amet consectetur adipiscing elit.</p>
    <a>Read More »</a>
  </article>
</section>

<section class="contact">
  <svg class="env" width="66" height="66" viewBox="0 0 66 66"><circle cx="33" cy="33" r="31" fill="none" stroke="#fff" stroke-width="2"/><rect x="19" y="23" width="28" height="20" rx="2" fill="#fff"/><path d="M19 24l14 11 14-11" fill="none" stroke="#0f1f52" stroke-width="2"/></svg>
  <h2>Contact Us</h2>
  <p class="lead">Please, Feel free to contact anytime. it's always<br>a pleasure meeting new student.</p>
  <div class="rule"></div>
  <h3 style="left:134px">Drop Your Question</h3>
  <div class="field" style="top:286px;height:36px">Name</div>
  <div class="field" style="top:338px;height:36px">Email</div>
  <div class="field" style="top:390px;height:78px">Message</div>
  <div class="send">SEND</div>
  <h3 style="left:496px">Location Map</h3>
  <div class="map"><div role="img" aria-label="Street map with a pin marking the college"></div></div>
  <h3 style="left:871px">Find Us</h3>
  <ul class="find" style="top:283px">
    <li><svg width="14" height="18" viewBox="0 0 14 18"><path d="M7 0a7 7 0 0 0-7 7c0 5 7 11 7 11s7-6 7-11a7 7 0 0 0-7-7z" fill="#fff"/><circle cx="7" cy="7" r="2.5" fill="#0f1f52"/></svg><span>123 euismod cidun ut laoreet<br>laoreet dol magna aliquam<br>PG Fesgalt</span></li>
    <li><svg width="14" height="16" viewBox="0 0 14 16"><path d="M3 1l3 3-2 2c1 2 3 4 5 5l2-2 3 3-2 3C6 15 0 9 1 3z" fill="#fff"/></svg>(123) 456 - 7890</li>
    <li><svg width="14" height="16" viewBox="0 0 14 16"><rect x="3" y="0" width="8" height="16" rx="2" fill="#fff"/></svg>(123) 456 - 7890</li>
    <li><svg width="14" height="12" viewBox="0 0 14 12"><rect width="14" height="11" rx="1" fill="#fff"/><path d="M0 1l7 5 7-5" fill="none" stroke="#0f1f52" stroke-width="1.5"/></svg>info@cedarvaleridge.ca</li>
    <li class="socials"><b></b><b></b><b></b><b></b></li>
  </ul>
</section>

<footer class="site-footer">Copyright © 2014 &nbsp;cedarvaleridge.ca . All Right Reserved</footer>

</body>
</html>
```